skincare creams for tired moms

I need a package and a logo design for a skincare company based in California called Petal Ledger. I make day and night cream, under eye cream, and body lotion. The first product I plan to launch is an under eye cream. It does not have to be in these colors but I do teals, greens, black, and cobalt blue.

The package is going to either be in a box or a bag. Either way I go it will be like a gift box or bag. The design should make the person feel like they are getting something special and luxurious just for them.
Updates

I have small kids and it is really difficult to find a chunk of time to myself to update or review.

Need extra days to review

Target Market(s)

mainly first time moms. I am making an under eye cream that does not use retinol but is still powerful enough to get rid of bags and dark circles.

Industry/Entity Type

Cosmetics

Logo Text

The package and logo should incorporate the name Petal Ledger.

Font styles to use
Decorative
Script

Colors

Designer to choose colors to be used in the design.

Requirements
Nice to have
• maybe focus more on Ledger instead of Petal. Also incorporate plants or flowers
Should not have
• not a huge fan of pink

```html
<!DOCTYPE html>
<html lang="en">
<head>
<meta charset="utf-8">
<title>Petal Ledger — Under Eye Cream Package</title>
<link rel="stylesheet" href="https://fonts.googleapis.com/css2?family=Abril+Fatface&family=Cormorant+Garamond:wght@400&family=Roboto+Condensed:wght@400&display=swap">
<style>
  :root {
    --page: #ffffff;
    --teal: #00918f;
    --teal-glow: #2fa58c;
    --teal-deep: #008a8a;
    --leaf-green: #68c187;
    --label-white: #ffffff;
    --cobalt: #3d4fb5;
    --soft-green: #a6dcb6;
  }
  html, body {
    margin: 0;
    padding: 0;
    width: 1200px;
    height: 1036px;
    overflow: hidden;
    background: var(--page);
  }
  .canvas {
    position: relative;
    width: 1200px;
    height: 1036px;
  }
  .package-front {
    position: absolute;
    left: 450px;
    top: 0;
    width: 314px;
    height: 1036px;
  }
  .package-art {
    position: absolute;
    inset: 0;
    display: block;
  }
  .brand-name {
    position: absolute;
    left: 0;
    width: 314px;
    top: 556px;
    margin: 0;
    text-align: center;
    font-family: "Abril Fatface", serif;
    font-weight: 400;
    font-size: 42px;
    line-height: 1;
    letter-spacing: 12px;
    padding-left: 12px;
    box-sizing: border-box;
    color: var(--teal);
  }
  .brand-sub {
    position: absolute;
    left: 0;
    width: 314px;
    top: 609px;
    margin: 0;
    text-align: center;
    font-family: "Cormorant Garamond", serif;
    font-size: 10px;
    letter-spacing: 9px;
    padding-left: 9px;
    box-sizing: border-box;
    color: var(--cobalt);
  }
  .product-name {
    position: absolute;
    left: 28px;
    top: 951px;
    margin: 0;
    font-family: "Cormorant Garamond", serif;
    font-size: 11px;
    letter-spacing: 9.6px;
    color: var(--soft-green);
    white-space: nowrap;
  }
  .product-size {
    position: absolute;
    left: 28px;
    top: 1006px;
    margin: 0;
    font-family: "Roboto Condensed", sans-serif;
    font-size: 10px;
    color: var(--label-white);
  }
</style>
</head>
<body>
<main class="canvas">
  <section class="package-front">
    <svg class="package-art" width="314" height="1036" viewBox="0 0 314 1036" xmlns="http://www.w3.org/2000/svg">
      <defs>
        <radialGradient id="floral-tone" cx="155" cy="300" r="330" gradientUnits="userSpaceOnUse">
          <stop offset="0" stop-color="var(--teal-glow)"/>
          <stop offset="0.55" stop-color="var(--teal)"/>
          <stop offset="1" stop-color="var(--teal-deep)"/>
        </radialGradient>
      </defs>
      <rect class="lower-band" x="0" y="682" width="314" height="354" fill="var(--leaf-green)"/>
      <rect class="floral-field" x="0" y="0" width="314" height="682" fill="url(#floral-tone)" role="img" aria-label="Symmetric line-drawn floral pattern in light green on teal"/>
      <polygon class="label-kite" points="155,381 303,549 162,844 11,549" fill="var(--label-white)"/>
      <circle class="brand-seal" cx="159" cy="507" r="48" fill="none" stroke="var(--leaf-green)" stroke-width="1.5"/>
    </svg>
    <h1 class="brand-name">PETAL</h1>
    <p class="brand-sub">LEDGER</p>
    <p class="product-name">UNDER EYE CREAM</p>
    <p class="product-size">0.5 OZ</p>
  </section>
</main>
</body>
</html>
```